Companybrochure for Consulting & Financing Firm

I need to have a Company Brochure asap for our company. We have a website that describes what we do, but we need also a brochure, that can be sent by PDF of eventually be printed as well.

The brochure should be short but nice and appealing to the customers.

We provide professional management consulting and help our customers to get finance for very diferent projects. Our business has a lot to do with personal relations, but also we are very professional in the way we work and how develop the solutions for our clients. Our clients are mainly government-owned firm, but also private trading companies and wealthy private investors.

Our customers are mainly in Latin America, but the company is headquater is in Switzerland. We are opening offices in Panama and Caracas, this should be easaly be adabtable later.

Please have a look at our website www.vorelpartners.ch. In the brochure, we would segment our services in 1.) Project Developments 2.) Management Conulting 3.) Investment Management and 4.) Finance Solutions.

Also do have a look at www.vorelpartners.ch
(Click E for the English version)
Updates

I managed to put the Mock-Up to the Website.
It is actually not really a mock-up, it is a version I have designed myself.
Well as I am not a designer, I hope you can make it much better.
The content however is what I would put in any other design as well.

Target Market(s)

Top Management, Investors, Entrepreneurs, Government Officials

Industry/Entity Type

Management Consulting

Requirements
Must have
• Design should reflect this image elements:

We are entrepreneurs.
We are comitted to get things done.
We work closely with the client side by side.
We are a professional partner.
We are not afraid of delivering unconventional solutions.
We look at the problem from various angles.
We analyse, develop solutions and implent results.
Should not have
• Typical US-American style elements. We do not want to give the impression of being a US company.

We do not want to appear to be neo-liberal. We are a politically neutral professional consulting firm.

```html
<!DOCTYPE html>
<html lang="en">
<head>
<meta charset="utf-8">
<title>Vorel Partners AG – Brochure</title>
<link href="https://fonts.googleapis.com/css2?family=Oswald:wght@500;600&family=Ubuntu:wght@300;500&family=Open+Sans:wght@600&display=swap" rel="stylesheet">
<style>
  :root{
    --bg:#e6e3df;
    --paper:#ffffff;
    --ink:#333333;
    --panel-dark:#333333;
    --navy:#2a2566;
    --navy-glass:rgba(42,37,102,.86);
    --white:#ffffff;
    --green-light:#d6ecb4;
    --green-mid:#9fd06a;
    --green-deep:#4c9a2a;
  }
  *{margin:0;padding:0;box-sizing:border-box}
  html,body{width:1200px;height:960px;overflow:hidden;background:var(--bg)}
  .spread{position:relative;width:1200px;height:960px}
  .page{position:absolute;top:99px;width:540px;height:762px;background:var(--paper);overflow:hidden}
  .page--back{left:40px}
  .page--front{left:610px}

  /* back page */
  .values-panel{position:absolute;left:191px;top:194px;width:349px;height:364px;background:var(--panel-dark);color:var(--white);
    clip-path:polygon(47px 0,100% 0,100% 290px,275px 100%,0 100%,0 88px);padding:90px 10px 0 15px}
  .values-panel__title{font-family:"Oswald",sans-serif;font-weight:500;font-size:26px;letter-spacing:.3px;white-space:nowrap;margin-bottom:10px}
  .values-list{list-style:none;font-family:"Ubuntu",sans-serif;font-weight:500;font-size:14px;line-height:15px}
  .values-list li{margin-bottom:10px;padding-left:12px;text-indent:-12px}
  .values-list li::before{content:"> "}
  .brand-name{font-family:"Open Sans",sans-serif;font-weight:600;color:var(--ink);font-size:22px;letter-spacing:.2px}
  .page--back .brand-name{position:absolute;left:194px;top:562px}
  .contact-box{position:absolute;left:0;top:361px;width:175px;height:183px;background:var(--navy);color:var(--white);
    clip-path:polygon(45px 0,100% 0,100% 148px,140px 100%,0 100%,0 0);padding:40px 0 0 24px;
    font-family:"Ubuntu",sans-serif;font-weight:500;font-size:11.5px;line-height:14px}
  .contact-box p{margin-bottom:9px}
  .registry-box{position:absolute;left:68px;top:555px;width:107px;height:111px;background:var(--navy);color:var(--white);
    clip-path:polygon(0 0,100% 0,100% 88px,84px 100%,0 100%);display:flex;align-items:center;justify-content:center;text-align:center;
    font-family:"Oswald",sans-serif;font-weight:500;font-size:12.5px;line-height:15.5px;padding:0 8px}

  /* front page */
  .cover-photo{position:absolute;left:28px;top:0;width:485px;height:730px;
    clip-path:polygon(0 0,100% 0,100% 670px,425px 100%,0 100%);
    background:
      radial-gradient(ellipse 40% 30% at 35% 55%,rgba(255,255,255,.85),rgba(255,255,255,0) 70%),
      linear-gradient(180deg,var(--green-light) 0%,#bfe08f 45%,var(--green-mid) 70%,var(--green-deep) 100%)}
  .page--front .brand-name{position:absolute;left:28px;width:485px;top:32px;text-align:center;font-size:35px}
  .services-box{position:absolute;left:176px;top:469px;width:229px;height:237px;background:var(--navy-glass);color:var(--white);
    clip-path:polygon(40px 0,100% 0,100% 100%,0 100%,0 40px);padding:58px 10px 0 20px}
  .services-box__intro{font-family:"Oswald",sans-serif;font-weight:500;font-size:16.5px;line-height:18.5px;text-align:justify;margin-bottom:10px}
  .services-list{list-style:none;font-family:"Ubuntu",sans-serif;font-weight:300;font-size:15.5px;line-height:20px}
  .services-list li::before{content:"> "}
  .motto-box{position:absolute;left:55px;top:592px;width:113px;height:116px;background:var(--panel-dark);color:var(--white);
    clip-path:polygon(0 0,96px 0,100% 17px,100% 100%,0 100%);display:flex;align-items:center;justify-content:center;text-align:center;
    font-family:"Oswald",sans-serif;font-weight:600;font-size:26px;line-height:30px;text-transform:uppercase;padding-top:6px}
</style>
</head>
<body>
<main class="spread">
  <section class="page page--back">
    <div class="values-panel">
      <h2 class="values-panel__title">ANALYZE &bull; DEVELOP &bull; DELIVER</h2>
      <ul class="values-list">
        <li>We are entrepreneurs.</li>
        <li>We are comitted to get things done.</li>
        <li>We work closely with the client side by side.</li>
        <li>We are a professional partner.</li>
        <li>We are not afraid of delivering unconventional solutions.</li>
        <li>We look at the problem from various angles</li>
        <li>We analyse, develop solutions and implent results.</li>
      </ul>
    </div>
    <p class="brand-name">Vorel Partners AG</p>
    <address class="contact-box" style="font-style:normal">
      <p>Vorel Partners AG<br>Lindenbach-Strasse 14<br>CH-8004 Zürich</p>
      <p>Tel.&nbsp; +41 44 210 55 30<br>Fax. +41 44 210 55 39</p>
      <p>www.vorelpartners.ch<br>info@vorelpartners.ch</p>
    </address>
    <div class="registry-box">Vorel Partners AG is registered as a Swiss stock corporation since 1995.</div>
  </section>

  <section class="page page--front">
    <div class="cover-photo" role="img" aria-label="Photo of dandelion seed heads in green grass with a swallowtail butterfly against a soft green background"></div>
    <h1 class="brand-name">Vorel Partners AG</h1>
    <div class="services-box">
      <p class="services-box__intro">We are a professional consulting, financing and investment firm operating in the fields of:</p>
      <ul class="services-list">
        <li>Project Development</li>
        <li>Management Consulting</li>
        <li>Investment Management</li>
        <li>Finance Solutions</li>
      </ul>
    </div>
    <div class="motto-box">Analyze<br>Develop<br>Deliver</div>
  </section>
</main>
</body>
</html>
```